Realtor branding business card

modern, simple and self branding. Broker office logo needs to be used but not emphasized. Looking to brand myself

Target Market(s)

buyers, sellers and investors

Industry/Entity Type

Realtor

Contact Information for Business Card

Sample of my current business card on file

Requirements
Must have
• my website - tobiasmerrowkl.com
• Realtor logo
• Fair housing logo
Nice to have
• Colors from office logo but not a must
Should not have
• Do not want headshot

```html
<!DOCTYPE html>
<html lang="en">
<head>
<meta charset="utf-8">
<title>Tobias Merrow – Realtor Business Card</title>
<link rel="stylesheet" href="https://fonts.googleapis.com/css2?family=Oswald:wght@500;700&family=Roboto:wght@400;500&display=swap">
<style>
  :root {
    --navy: #2e2a70;
    --red: #e0262b;
    --ink-grey: #6f6f76;
    --paper: #ffffff;
    --backdrop: #d9d9d9;
    --map-tone: #ececf0;
    --badge-tone: #ffffff;
  }
  * { margin: 0; padding: 0; box-sizing: border-box; }
  html, body {
    width: 1200px; height: 930px; overflow: hidden;
    background: var(--backdrop);
    font-family: "Roboto", Arial, sans-serif;
  }
  .canvas { position: relative; width: 1200px; height: 930px; }

  .card {
    position: absolute; left: 290px; width: 620px; height: 354px;
    overflow: hidden;
    box-shadow: 0 6px 18px rgba(0,0,0,.18);
  }

  /* Back of card */
  .card-back { top: 70px; background: var(--navy); }
  .card-back .back-agent {
    position: absolute; left: 0; right: 0; top: 112px;
    text-align: center; color: var(--paper);
    font-family: "Oswald", Arial, sans-serif; font-weight: 500;
    font-size: 42px; line-height: 1; letter-spacing: 2px;
  }
  .card-back .brand-name {
    position: absolute; left: 0; right: 0; top: 172px;
    text-align: center; color: var(--paper);
    font-family: "Oswald", Arial, sans-serif; font-weight: 500;
    font-size: 18px; line-height: 1; letter-spacing: 1px;
  }
  .card-back .back-website {
    position: absolute; left: 0; right: 0; top: 262px;
    text-align: center; color: var(--paper);
    font-size: 14px; letter-spacing: .4px;
  }

  /* Front of card */
  .card-front { top: 496px; background: var(--paper); }
  .world-map {
    position: absolute; left: 200px; top: 20px; width: 360px; height: 200px;
    background: radial-gradient(ellipse at center, var(--map-tone) 0%, rgba(236,236,240,0) 70%);
  }
  .front-brand {
    position: absolute; left: 44px; top: 58px;
    display: flex; align-items: center; gap: 8px;
    color: var(--navy);
    font-family: "Oswald", Arial, sans-serif; font-weight: 500;
    font-size: 22px; line-height: 1;
  }
  .front-brand .brand-square { width: 13px; height: 13px; background: var(--navy); }

  .agent { position: absolute; left: 44px; top: 182px; }
  .agent-name {
    font-family: "Oswald", Arial, sans-serif; font-weight: 500;
    font-size: 36px; color: var(--navy); letter-spacing: 1.5px; line-height: 1.05;
  }
  .agent-title { font-size: 15px; color: var(--ink-grey); margin-top: 2px; }
  .agent-address { font-size: 14px; color: var(--ink-grey); margin-top: 10px; line-height: 1.45; }

  .contacts {
    position: absolute; left: 360px; top: 150px; list-style: none;
    font-size: 14.5px; color: var(--ink-grey);
  }
  .contacts li { display: flex; align-items: center; gap: 12px; height: 27px; }
  .contacts svg { width: 14px; height: 14px; flex: none; }
  .contacts .accent { color: var(--red); }

  .bottom-band {
    position: absolute; left: 0; right: 0; bottom: 0; height: 34px;
    background: var(--navy);
  }
  .badges {
    position: absolute; right: 20px; top: 7px;
    display: flex; gap: 8px;
  }
  .badge { width: 20px; height: 20px; background: var(--badge-tone); }
</style>
</head>
<body>
<main class="canvas">

  <section class="card card-back" aria-label="Card back">
    <p class="back-agent">TOBIAS MERROW</p>
    <p class="brand-name">Brightline Realty Group</p>
    <p class="back-website">www.tobiasmerrowkl.com</p>
  </section>

  <section class="card card-front" aria-label="Card front">
    <div class="world-map" role="img" aria-label="Faint dotted world map in the background"></div>

    <div class="front-brand">
      <span class="brand-square"></span>
      <span>Brightline Realty Group</span>
    </div>

    <div class="agent">
      <h1 class="agent-name">TOBIAS MERROW</h1>
      <p class="agent-title">Realtor</p>
      <p class="agent-address">482 Harbor Oak Lane<br>Lake Sorrel, FL 32799</p>
    </div>

    <ul class="contacts">
      <li>
        <svg viewBox="0 0 14 14" aria-hidden="true"><rect x="3.5" y="1" width="7" height="12" rx="1.5" fill="none" stroke="#2e2a70" stroke-width="1.4"/><circle cx="7" cy="10.6" r=".8" fill="#2e2a70"/></svg>
        <span>407. 555. 0142</span>
      </li>
      <li>
        <svg viewBox="0 0 14 14" aria-hidden="true"><path d="M3 1.5l2.2 2.6-1.2 1.6c.8 1.8 2.2 3.2 4 4l1.6-1.2 2.6 2.2-1.4 1.8C6 12.2 1.8 8 1.5 3z" fill="#2e2a70"/></svg>
        <span>407. 555. 0190</span>
      </li>
      <li>
        <svg viewBox="0 0 14 14" aria-hidden="true"><rect x="1" y="3" width="12" height="8.5" fill="none" stroke="#2e2a70" stroke-width="1.3"/><path d="M1 3l6 5 6-5" fill="none" stroke="#2e2a70" stroke-width="1.3"/></svg>
        <span>info@tobiasmerrowkl.com</span>
      </li>
      <li>
        <svg viewBox="0 0 14 14" aria-hidden="true"><circle cx="7" cy="7" r="5.8" fill="none" stroke="#2e2a70" stroke-width="1.2"/><ellipse cx="7" cy="7" rx="2.5" ry="5.8" fill="none" stroke="#2e2a70" stroke-width="1.1"/><path d="M1.2 7h11.6" stroke="#2e2a70" stroke-width="1.1"/></svg>
        <span>www.<span class="accent">tobiasmerrowkl</span>.com</span>
      </li>
    </ul>

    <div class="bottom-band">
      <div class="badges">
        <span class="badge" role="img" aria-label="Realtor association badge"></span>
        <span class="badge" role="img" aria-label="Equal housing opportunity badge"></span>
      </div>
    </div>
  </section>

</main>
</body>
</html>
```